Brightwave Reach - Business Card

We need a business card for a Social Media Marketing company that specializes in online marketing for small businesses in Canada using common Social Media platforms such as Pixlora, Chatterly, Blinkpost & Quibber.

I have uploaded a copy of our logo which I would like utilized in the business card. We would like the business card to be modern yet classy design.

Our website is www.brightwavereach.ca

Industry/Entity Type

Marketing

Contact Information for Business Card

Email: info@brightwavereach.ca
Website: www.brightwavereach.ca
Telephone: 604-555-0193

Colors

Designer to choose colors to be used in the design.

Requirements
Must have
• Social Media icons on reverse
• Please add some designs with color.

```html
<!DOCTYPE html>
<html lang="en">
<head>
<meta charset="utf-8">
<title>Brightwave Reach – Business Card</title>
<link rel="stylesheet" href="https://fonts.googleapis.com/css2?family=Roboto:wght@400;500;700&display=swap">
<style>
  :root {
    --backdrop: #2b2b2b;
    --card: #f3f3f3;
    --ink: #3d4144;
    --band: #3d4144;
    --arc: #b3b3b3;
    --light-text: #f2f2f2;
    --rule: #8a8a8a;
  }
  * { margin: 0; padding: 0; box-sizing: border-box; }
  html, body {
    width: 1200px; height: 960px; overflow: hidden;
    background: var(--backdrop);
    font-family: "Roboto", Arial, sans-serif;
  }
  .canvas { position: relative; width: 1200px; height: 960px; }
  .card {
    position: absolute; width: 600px; height: 343px;
    background: var(--card); overflow: hidden;
    box-shadow: 0 3px 8px rgba(0,0,0,.45);
  }
  .card-front { left: 314px; top: 113px; }
  .card-back { left: 311px; top: 472px; }

  .brand {
    position: absolute; left: 0; right: 0; top: 70px;
    display: flex; justify-content: center; align-items: center; gap: 12px;
  }
  .brand-mark { width: 14px; height: 14px; background: var(--ink); }
  .brand-name {
    color: var(--ink); font-weight: 700; font-size: 30px; line-height: 1.05;
    text-transform: uppercase; text-align: center; letter-spacing: .5px;
  }

  .band { position: absolute; left: 0; top: 0; width: 600px; height: 343px; }

  .identity {
    position: absolute; left: 0; right: 0; top: 268px;
    text-align: center; color: var(--light-text);
  }
  .identity .person { font-size: 20px; font-weight: 500; text-transform: uppercase; }
  .identity .role { font-size: 15px; font-weight: 400; text-transform: uppercase; margin-left: 6px; }
  .contact { margin-top: 8px; font-size: 14.5px; font-weight: 400; }

  .emblem {
    position: absolute; left: 235px; top: 105px; width: 130px; height: 130px;
    border-radius: 50%; background: var(--ink);
  }
  .socials {
    position: absolute; left: 130px; right: 130px; top: 288px;
    display: flex; align-items: center; gap: 12px;
  }
  .socials .rule { flex: 1; height: 1px; background: var(--rule); }
  .socials .networks { color: var(--ink); font-size: 13px; font-weight: 500; letter-spacing: .3px; white-space: nowrap; }
</style>
</head>
<body>
<main class="canvas">
  <section class="card card-front" aria-label="Card front">
    <div class="brand">
      <span class="brand-mark"></span>
      <span class="brand-name">Brightwave<br>Reach</span>
    </div>
    <svg class="band" viewBox="0 0 600 343" aria-hidden="true">
      <path d="M0,194 Q300,266 600,194 V343 H0 Z" fill="var(--arc)"/>
      <path d="M0,197 Q300,278 600,197 V343 H0 Z" fill="var(--band)"/>
    </svg>
    <div class="identity">
      <span class="person">Daniel Hart&nbsp; -</span><span class="role">CEO/Founder</span>
      <p class="contact">604-555-0193 | info@brightwavereach.ca | www.brightwavereach.ca</p>
    </div>
  </section>

  <section class="card card-back" aria-label="Card back">
    <div class="emblem" role="img" aria-label="Brand emblem area"></div>
    <div class="socials">
      <span class="rule"></span>
      <span class="networks">Chatterly · Pixlora · Quibber</span>
      <span class="rule"></span>
    </div>
  </section>
</main>
</body>
</html>
```